BrivoTerna. Lantern of the Steady Harvest. Business card

Professional business card for BrivoTerna (Lantern of the Steady Harvest)
My rationale: Strategy-> Execution-> Results-> Value that lead to the BrivoTerna name: We put the Lantern of the Steady Harvest.
We deliver value to our customers helping them at defining a good strategy (cyan arrow). 90% of well formulated strategies fail due to poor execution so we also consider strategical execution very important (green arrow). Due to the execution we obtain the results (blue arrow). Finally, the results provide feedback to redefine strategy, and the new strategy has to be executed and new results obtained providing new feedback and on and on. It's like a wheel that finally, must create corporate value: value for shareholders, staholders, employees, providers...-

Target Market(s)

CEOs and steering comitees , invewrnent funds

Industry/Entity Type

Business Consultant

Contact Information for Business Card

Teodoro Vinsquel
CEO & Founder
teodoro.vinsquel@brivoterna-example.com
Mobile: +34 655.803.912
www.brivoterna-example.com

Colors

Designer to choose colors to be used in the design.

Requirements
Nice to have
• Nice to hace the words: Strategy, execution, results
• Nice to vave the claim: Lantern of the Steady Harvest
• The three colors should be shown:
• cyan for STRATEGY
• green for EXECUTION
• blue for RESULTS
Should not have
• Complete black background

```html
<!DOCTYPE html>
<html lang="en">
<head>
<meta charset="utf-8">
<title>BrivoTerna — Business Card</title>
<link rel="stylesheet" href="https://fonts.googleapis.com/css2?family=Montserrat:wght@400;500;600;700&display=swap">
<style>
  :root {
    --navy: #213785;
    --cyan: #14a3d8;
    --green: #8dbb35;
    --paper: #f4f4f3;
    --ink-grey: #6d6d70;
    --backdrop: #e8e8e7;
    --white: #ffffff;
  }
  * { margin: 0; padding: 0; box-sizing: border-box; }
  html, body {
    width: 1200px; height: 1200px; overflow: hidden;
    background: var(--backdrop);
    font-family: "Montserrat", Arial, sans-serif;
  }
  .card {
    position: absolute; left: 227px; width: 746px; height: 425px;
    border-radius: 38px; overflow: hidden;
  }
  .card--front { top: 135px; background: var(--paper); }
  .card--back { top: 640px; background: var(--navy); }

  .brand {
    position: absolute; left: 0; right: 0;
    display: flex; align-items: center; justify-content: center; gap: 14px;
    font-weight: 700; letter-spacing: -0.5px;
  }
  .brand__dot { width: 18px; height: 18px; border-radius: 50%; }
  .card--front .brand { top: 120px; font-size: 46px; color: var(--navy); }
  .card--front .brand__dot { background: var(--navy); }
  .card--back .brand { top: 228px; font-size: 56px; color: var(--white); }
  .card--back .brand__dot { background: var(--white); }

  .person {
    position: absolute; top: 216px; left: 0; right: 0; text-align: center;
  }
  .person__name { font-size: 21px; font-weight: 600; color: var(--navy); }
  .person__title { font-size: 16px; font-weight: 400; color: var(--ink-grey); margin-top: 2px; }

  .contacts {
    position: absolute; top: 286px; left: 0; right: 0;
    display: flex; justify-content: center; align-items: center; gap: 16px;
    font-size: 15px; color: var(--ink-grey);
  }
  .contact { display: flex; align-items: center; gap: 9px; }
  .contact svg { width: 17px; height: 17px; }
  .website {
    position: absolute; top: 314px; left: 0; right: 0; text-align: center;
    font-size: 15px; color: var(--ink-grey);
  }
  .website__domain { color: var(--navy); }

  .process-band { position: absolute; top: 352px; left: 0; width: 746px; height: 38px; }
  .process-band text {
    font-family: "Montserrat", Arial, sans-serif; font-size: 19px; font-weight: 600;
    fill: var(--white); text-anchor: middle;
  }

  .tagline {
    position: absolute; top: 302px; left: 0; right: 0; text-align: center;
    font-size: 18px; font-weight: 400; color: var(--white); letter-spacing: 0.3px;
  }
</style>
</head>
<body>

<section class="card card--front">
  <div class="brand"><span class="brand__dot"></span>BrivoTerna</div>

  <div class="person">
    <div class="person__name">Teodoro Vinsquel</div>
    <div class="person__title">CEO &amp; Founder</div>
  </div>

  <div class="contacts">
    <span class="contact">
      <svg viewBox="0 0 20 20" aria-hidden="true">
        <circle cx="10" cy="10" r="10" fill="var(--cyan)"/>
        <path d="M5 8.5c0-2 2.5-3 5-3s5 1 5 3l-1.6.6-.8-1.6H7.4l-.8 1.6z M7 10h6l1 4H6z" fill="var(--white)"/>
      </svg>
      +34 655.803.912
    </span>
    <span class="contact">
      <svg viewBox="0 0 20 20" aria-hidden="true">
        <circle cx="10" cy="10" r="10" fill="var(--green)"/>
        <rect x="5" y="6.5" width="10" height="7" fill="none" stroke="var(--white)" stroke-width="1.3"/>
        <path d="M5 6.5l5 4 5-4" fill="none" stroke="var(--white)" stroke-width="1.3"/>
      </svg>
      teodoro.vinsquel@brivoterna-example.com
    </span>
  </div>
  <div class="website">www.<span class="website__domain">brivoterna-example</span>.com</div>

  <svg class="process-band" viewBox="0 0 746 38" aria-label="Strategy, Execution, Results">
    <rect x="0" y="0" width="746" height="38" fill="var(--navy)"/>
    <polygon points="222,0 477,0 501,19 477,38 222,38 246,19" fill="var(--green)" stroke="var(--white)" stroke-width="3"/>
    <polygon points="-4,0 222,0 246,19 222,38 -4,38" fill="var(--cyan)" stroke="var(--white)" stroke-width="3"/>
    <text x="123" y="26">STRATEGY</text>
    <text x="363" y="26">EXECUTION</text>
    <text x="614" y="26">RESULTS</text>
  </svg>
</section>

<section class="card card--back">
  <div class="brand"><span class="brand__dot"></span>BrivoTerna</div>
  <div class="tagline">Lantern of the Steady Harvest</div>
</section>

</body>
</html>
```